Mobile Friendly Lead Generation Landing Page

We are a web marketing company that specialized in web lead generation. Recently we have started buying media from mobile devices and we need a mobile interface(landing page) where we can collect user data in an effective manner.

Our current mobile landing page is:
http://www.tutorpath.example.com/lp13d/index.aspx?a=true&source=841356
Through this you can see what the steps/questions users need to answer to get matched to a school. We need the design for the whole process.

We are pretty open for design ideas and our goal is to make this mobile optimized landing page have the look and feel of an app...but not an app.
There are several questions in the process but we are open to changing the way they are presented. As in, you can have one question at a time or a few.
The goal is to make this EXTREMELY EASY for users to interact with.

One example that we have liked is:
http://learnvane.example/schools/57214-page1.lvne (please note that this opens only on mobile devices)

Some of these screenshots are attached.

Our web form looks like this:
http://www.tutorpath.example.com/lp88/index.aspx?a=true

```html
<!DOCTYPE html>
<html lang="en">
<head>
<meta charset="utf-8">
<title>Main Screen</title>
<link href="https://fonts.googleapis.com/css2?family=Roboto:wght@300;400;500&display=swap" rel="stylesheet">
<style>
  :root {
    --page-bg: #eef4ea;
    --chrome-blue: #1b9cf2;
    --url-field: #86d0f8;
    --cta-yellow: #fdc300;
    --section-red: #ee2125;
    --icon-green: #17c93a;
    --row-bg: #ffffff;
    --row-line: #d9d9d9;
    --text-dark: #2a2a2a;
    --chevron: #6d6d6d;
    --white: #ffffff;
  }
  * { box-sizing: border-box; margin: 0; padding: 0; }
  html, body {
    width: 800px; height: 1200px; overflow: hidden;
    background: var(--page-bg);
    font-family: "Roboto", "Helvetica Neue", Arial, sans-serif;
  }
  .screen {
    position: absolute; left: 100px; top: 75px;
    width: 600px; height: 1050px;
    background: #f4f2ef;
    display: flex; flex-direction: column;
    box-shadow: 0 6px 30px rgba(0,0,0,.12);
    overflow: hidden;
  }
  .browser-header { background: var(--chrome-blue); color: var(--white); }
  .status-bar {
    height: 42px; display: flex; align-items: center; justify-content: space-between;
    padding: 0 18px; font-size: 19px;
  }
  .status-left { display: flex; align-items: center; gap: 8px; }
  .signal { display: flex; gap: 3px; }
  .signal span { width: 9px; height: 9px; border-radius: 50%; border: 1.5px solid var(--white); }
  .signal span.on { background: var(--white); }
  .status-right { display: flex; align-items: center; gap: 8px; }
  .battery { width: 42px; height: 17px; border: 1.5px solid var(--white); border-radius: 3px; padding: 2px; position: relative; }
  .battery::before { content: ""; display: block; height: 100%; background: var(--white); border-radius: 1px; }
  .battery::after { content: ""; position: absolute; right: -5px; top: 4px; width: 3px; height: 6px; background: var(--white); border-radius: 0 2px 2px 0; }
  .url-row { height: 80px; padding: 10px 14px 18px; }
  .url-field {
    height: 100%; background: var(--url-field); border-radius: 8px;
    display: flex; align-items: center; justify-content: center; position: relative;
    font-size: 27px; font-weight: 300;
  }
  .url-field svg { position: absolute; right: 14px; top: 50%; transform: translateY(-50%); }
  .pastel-strip {
    background: linear-gradient(90deg, #f0d6d6 0%, #ddd9cf 35%, #d4d4d6 55%, #dcece0 100%);
  }
  .strip-top { height: 38px; }
  .strip-mid { height: 30px; }
  .strip-bottom { flex: 1; background: linear-gradient(90deg, #d8e0ec 0%, #ece6d6 50%, #f7ead0 100%); }
  .band {
    height: 80px; display: flex; align-items: center; justify-content: center;
    color: var(--white); font-size: 27px; text-transform: uppercase; letter-spacing: .2px;
  }
  .band-cta { background: var(--cta-yellow); }
  .band-section { background: var(--section-red); height: 84px; }
  .offer {
    height: 87px; background: var(--row-bg); display: flex; align-items: center; justify-content: center;
    font-size: 24px; font-weight: 300; color: var(--text-dark);
  }
  .interest-list { list-style: none; background: var(--row-bg); }
  .interest-item {
    height: 79px; display: flex; align-items: center; padding: 0 22px 0 30px;
    border-bottom: 1px solid var(--row-line); font-size: 23px; color: var(--text-dark);
  }
  .interest-item:last-child { border-bottom: none; }
  .interest-icon {
    width: 54px; height: 54px; border-radius: 9px; background: var(--icon-green);
    display: flex; align-items: center; justify-content: center; margin-right: 18px; flex: none;
  }
  .interest-label { flex: 1; }
  .browser-toolbar {
    height: 84px; background: var(--chrome-blue);
    display: flex; align-items: center; justify-content: space-around;
  }
</style>
</head>
<body>
<main class="screen">
  <header class="browser-header">
    <div class="status-bar">
      <div class="status-left">
        <div class="signal"><span class="on"></span><span class="on"></span><span class="on"></span><span></span><span></span></div>
        <span>Northwave</span>
        <svg width="22" height="16" viewBox="0 0 22 16"><path d="M2 6a13 13 0 0 1 18 0M5 9.5a8.5 8.5 0 0 1 12 0M8 13a4 4 0 0 1 6 0" fill="none" stroke="#fff" stroke-width="2.2" stroke-linecap="round"/></svg>
      </div>
      <span>4:21 PM</span>
      <div class="status-right"><span>100%</span><div class="battery"></div></div>
    </div>
    <div class="url-row">
      <div class="url-field">tutorpath.example.com
        <svg width="26" height="26" viewBox="0 0 26 26"><path d="M20 13a7 7 0 1 1-2.2-5.1" fill="none" stroke="#fff" stroke-width="2.4"/><path d="M15 4h5v5" fill="none" stroke="#fff" stroke-width="2.4"/></svg>
      </div>
    </div>
  </header>

  <div class="pastel-strip strip-top"></div>
  <div class="band band-cta">Complete our 3-minute app</div>
  <p class="offer">Get up to $5, 645* per year in Grants if you qualify</p>
  <div class="pastel-strip strip-mid"></div>
  <h2 class="band band-section" style="font-weight:400">Select area of your interest</h2>

  <ul class="interest-list">
    <li class="interest-item">
      <span class="interest-icon"><svg width="34" height="34" viewBox="0 0 34 34" fill="none" stroke="#fff" stroke-width="1.8" stroke-linecap="round"><path d="M28 4 14 20M12 21c-4 1-4 5-7 8 5 0 9-1 10-5z"/></svg></span>
      <span class="interest-label">Art &amp; Design</span>
      <svg width="14" height="22" viewBox="0 0 14 22"><path d="M3 3l8 8-8 8" fill="none" stroke="var(--chevron)" stroke-width="2.4"/></svg>
    </li>
    <li class="interest-item">
      <span class="interest-icon"><svg width="34" height="34" viewBox="0 0 34 34" fill="none" stroke="#fff" stroke-width="1.8"><rect x="5" y="10" width="24" height="17" rx="1"/><path d="M13 10V6h8v4M5 17h24M15 17v3h4v-3"/></svg></span>
      <span class="interest-label">Business</span>
      <svg width="14" height="22" viewBox="0 0 14 22"><path d="M3 3l8 8-8 8" fill="none" stroke="var(--chevron)" stroke-width="2.4"/></svg>
    </li>
    <li class="interest-item">
      <span class="interest-icon"><svg width="34" height="34" viewBox="0 0 34 34" fill="none" stroke="#fff" stroke-width="1.8" stroke-linecap="round"><path d="M10 8l8 8M14 5l7 7M11 7l6-3 5 5-3 6M15 13l-9 9M17 27h12"/></svg></span>
      <span class="interest-label">Criminal Justice</span>
      <svg width="14" height="22" viewBox="0 0 14 22"><path d="M3 3l8 8-8 8" fill="none" stroke="var(--chevron)" stroke-width="2.4"/></svg>
    </li>
    <li class="interest-item">
      <span class="interest-icon"><svg width="40" height="40" viewBox="0 0 40 40"><text x="20" y="16" text-anchor="middle" font-size="11" fill="#fff" font-family="Roboto, sans-serif">ABC</text><line x1="5" y1="20" x2="35" y2="20" stroke="#fff" stroke-width="1.2"/><text x="20" y="32" text-anchor="middle" font-size="11" fill="#fff" font-family="Roboto, sans-serif">1 2 3</text></svg></span>
      <span class="interest-label">Education &amp; Teaching</span>
      <svg width="14" height="22" viewBox="0 0 14 22"><path d="M3 3l8 8-8 8" fill="none" stroke="var(--chevron)" stroke-width="2.4"/></svg>
    </li>
    <li class="interest-item">
      <span class="interest-icon"><svg width="34" height="34" viewBox="0 0 34 34" fill="none" stroke="#fff" stroke-width="1.8" stroke-linecap="round"><circle cx="17" cy="7" r="2.5"/><path d="M16 9 8 29M18 9l8 20M10 22h14"/></svg></span>
      <span class="interest-label">Engineering</span>
      <svg width="14" height="22" viewBox="0 0 14 22"><path d="M3 3l8 8-8 8" fill="none" stroke="var(--chevron)" stroke-width="2.4"/></svg>
    </li>
    <li class="interest-item">
      <span class="interest-icon"><svg width="34" height="34" viewBox="0 0 34 34" fill="none" stroke="#fff" stroke-width="1.8" stroke-linejoin="round"><path d="M17 11c-4-3-9-3-12-2v16c3-1 8-1 12 2 4-3 9-3 12-2V9c-3-1-8-1-12 2zM17 11v16"/></svg></span>
      <span class="interest-label">Other</span>
      <svg width="14" height="22" viewBox="0 0 14 22"><path d="M3 3l8 8-8 8" fill="none" stroke="var(--chevron)" stroke-width="2.4"/></svg>
    </li>
  </ul>

  <div class="strip-bottom"></div>

  <nav class="browser-toolbar">
    <svg width="20" height="32" viewBox="0 0 20 32"><path d="M16 3 4 16l12 13" fill="none" stroke="#fff" stroke-width="2.2"/></svg>
    <svg width="20" height="32" viewBox="0 0 20 32"><path d="M4 3l12 13L4 29" fill="none" stroke="#fff" stroke-width="2.2"/></svg>
    <svg width="30" height="38" viewBox="0 0 30 38" fill="none" stroke="#fff" stroke-width="2"><path d="M10 14H4v22h22V14h-6M15 24V2M9 8l6-6 6 6"/></svg>
    <svg width="38" height="32" viewBox="0 0 38 32" fill="none" stroke="#fff" stroke-width="2" stroke-linejoin="round"><path d="M19 6C14 2 7 2 2 4v24c5-2 12-2 17 2 5-4 12-4 17-2V4c-5-2-12-2-17 2zM19 6v24"/></svg>
    <svg width="36" height="36" viewBox="0 0 36 36" fill="none" stroke="#fff" stroke-width="2"><rect x="3" y="11" width="22" height="22"/><path d="M11 11V3h22v22h-8"/></svg>
  </nav>
</main>
</body>
</html>
```